Need help in designing new business card utilizing our new logo.

BuildMark Solutions works with Construction Business Owners, Managers & IT Professionals to strengthen software usage and increase user productivity.

Our Construction Accounting and Mobile Field Management Software Clients engage with us in the following areas:

New Software Implementations
Software Re-Implementations
Redesigning Software Usage at the User Level
Project Coordination & Management
Continued Software Support

Old tag line:
Weighing Options - Implementing Solutions

www.buildmark-solutions.example

Ridge 4 is a product, but not needed for a new business card.

```html
<!DOCTYPE html>
<html lang="en">
<head>
<meta charset="utf-8">
<title>BuildMark Solutions – Business Card</title>
<link rel="stylesheet" href="https://fonts.googleapis.com/css2?family=Montserrat:wght@400;500;600;700&display=swap">
<style>
  :root {
    --brand-blue: #2a35a3;
    --brand-blue-deep: #1f2a8c;
    --ink: #3a3a3a;
    --grey-band: #c9c9cc;
    --card-white: #ffffff;
    --backdrop: #e4e5e8;
    --on-blue: #e9ebf6;
  }
  * { box-sizing: border-box; margin: 0; padding: 0; }
  html, body { width: 1200px; height: 900px; overflow: hidden; }
  body {
    background: var(--backdrop);
    font-family: "Montserrat", sans-serif;
    display: flex;
    flex-direction: column;
    align-items: center;
    justify-content: center;
    gap: 40px;
  }
  .card {
    position: relative;
    width: 700px;
    height: 400px;
    border-radius: 22px;
    overflow: hidden;
    box-shadow: 0 6px 18px rgba(0,0,0,0.15);
  }

  /* Front */
  .card-front { background: linear-gradient(160deg, #f2f2f3 0%, var(--card-white) 45%); color: var(--ink); }
  .front-brand {
    position: absolute; left: 60px; top: 40px;
    display: flex; align-items: center; gap: 14px;
  }
  .brand-square { width: 40px; height: 40px; background: var(--brand-blue); }
  .brand-name { font-size: 34px; font-weight: 700; color: var(--brand-blue); letter-spacing: 0.5px; }
  .front-tagline {
    position: absolute; left: 60px; top: 112px;
    font-size: 19px; font-weight: 600; color: var(--brand-blue); line-height: 1.25;
  }
  .front-rule {
    position: absolute; left: 60px; right: 60px; top: 176px;
    height: 2px; background: var(--brand-blue);
  }
  .contact-list {
    position: absolute; left: 60px; top: 192px;
    list-style: none; font-size: 15px; line-height: 26px; color: var(--ink);
  }
  .contact-list li { display: flex; align-items: center; gap: 10px; }
  .contact-list svg { width: 12px; height: 12px; fill: var(--brand-blue); flex: none; }
  .person {
    position: absolute; right: 60px; top: 190px; text-align: right;
  }
  .person-name { font-size: 28px; font-weight: 700; color: var(--brand-blue); }
  .person-title { font-size: 15px; font-weight: 500; color: var(--ink); margin-top: 2px; }
  .person-address { font-size: 15px; line-height: 22px; margin-top: 14px; color: var(--ink); }
  .front-swoosh { position: absolute; left: 0; bottom: 0; width: 700px; height: 140px; }

  /* Back */
  .card-back {
    background: linear-gradient(135deg, var(--brand-blue) 0%, var(--brand-blue-deep) 100%);
    color: var(--on-blue);
  }
  .back-brand {
    position: absolute; right: 60px; top: 56px;
    display: flex; align-items: center; gap: 16px;
  }
  .back-brand .brand-square { background: var(--on-blue); width: 46px; height: 46px; }
  .back-brand .brand-name { color: var(--on-blue); font-size: 40px; }
  .service-list {
    position: absolute; left: 60px; right: 60px; top: 190px;
    list-style: none; text-align: center;
    font-size: 18px; font-weight: 500; line-height: 34px;
  }
</style>
</head>
<body>

<section class="card card-front" aria-label="Business card front">
  <div class="front-brand">
    <span class="brand-square"></span>
    <span class="brand-name">BuildMark Solutions</span>
  </div>
  <p class="front-tagline">Construction Accounting<br>Software Consultants</p>
  <div class="front-rule"></div>

  <ul class="contact-list">
    <li><svg viewBox="0 0 12 12"><path d="M2.5 0.5l2 2-1 1.5c.8 1.6 2 2.8 3.5 3.5l1.5-1 2 2-1.5 2C5 11.5 0.5 7 0.5 2z"/></svg>866-555-0142 ext.100</li>
    <li><svg viewBox="0 0 12 12"><path d="M3 0h6a1 1 0 011 1v10a1 1 0 01-1 1H3a1 1 0 01-1-1V1a1 1 0 011-1zm0 1.5v8h6v-8z"/></svg>518-555-0187</li>
    <li><svg viewBox="0 0 12 12"><path d="M0 2h12v8H0zm1 1v.3l5 3.4 5-3.4V3zm0 1.5V9h10V4.5L6 8z"/></svg>dana.whitfield@buildmark-solutions.example</li>
    <li><svg viewBox="0 0 12 12"><circle cx="6" cy="6" r="5.5"/></svg>www.buildmark-solutions.example</li>
  </ul>

  <div class="person">
    <p class="person-name">Dana R. Whitfield</p>
    <p class="person-title">Owner</p>
    <p class="person-address">48 Linden Avenue Suite 12<br>Millbrook NY 12000</p>
  </div>

  <svg class="front-swoosh" viewBox="0 0 700 140" preserveAspectRatio="none" aria-hidden="true">
    <path d="M0 20 C180 60 420 120 700 118 L700 140 L0 140 Z" fill="var(--grey-band)"/>
    <path d="M0 40 C200 80 430 130 700 130 L700 140 L0 140 Z" fill="var(--brand-blue)"/>
  </svg>
</section>

<section class="card card-back" aria-label="Business card back">
  <div class="back-brand">
    <span class="brand-square"></span>
    <span class="brand-name">BuildMark Solutions</span>
  </div>
  <ul class="service-list">
    <li>New Software Implementations | Software Re-Implementations</li>
    <li>Redesigning Software Usage at the User Level</li>
    <li>Project Coordination &amp; Management</li>
    <li>Continued Software Support</li>
  </ul>
</section>

</body>
</html>
```